Create a memorable Stationary for Security Software Company

Velbrantix is the worldwide leader in securing the Internet. Making Internet communications and critical data secure, reliable and available everywhere has been and continues to be our ongoing vision. We are committed to staying focused on real customer needs and to developing new and innovative security solutions that redefine the security landscape.

Industry/Entity Type

Internet

Font styles to use
Serif
Sans Serif
Script

Colors
0792cd
33a6d7
85cae6

```html
<!DOCTYPE html>
<html lang="en">
<head>
<meta charset="utf-8">
<title>Velbrantix Business Card</title>
<link rel="stylesheet" href="https://fonts.googleapis.com/css2?family=Source+Sans+3:wght@400;600&display=swap">
<style>
  :root {
    --brand-deep: #0792cd;
    --brand-mid: #33a6d7;
    --brand-light: #85cae6;
    --card-black: #141516;
    --text-light: #e9edf0;
    --divider: #55595d;
    --backdrop: #3a3634;
  }
  * { box-sizing: border-box; margin: 0; padding: 0; }
  html, body { width: 1200px; height: 814px; overflow: hidden; }
  body {
    background: var(--backdrop);
    font-family: "Source Sans 3", sans-serif;
    position: relative;
  }
  .card {
    position: absolute;
    top: 237px;
    width: 540px;
    height: 340px;
    background: var(--card-black);
    border-radius: 4px;
    box-shadow: 0 10px 30px rgba(0,0,0,.45);
  }
  .card-contact { left: 45px; }
  .card-brand { left: 615px; }

  .contact-mark {
    position: absolute;
    left: 70px; top: 95px;
    width: 150px; height: 150px;
    border-radius: 50%;
    background: radial-gradient(circle at 40% 35%, var(--brand-light), var(--brand-mid) 55%, var(--brand-deep));
  }
  .contact-divider {
    position: absolute;
    left: 280px; top: 60px;
    width: 1px; height: 220px;
    background: linear-gradient(to bottom, transparent, var(--divider) 20%, var(--divider) 80%, transparent);
  }
  .contact-details {
    position: absolute;
    left: 305px; top: 74px;
    color: var(--text-light);
    font-size: 15px;
    line-height: 1.3;
  }
  .person-name { color: var(--brand-deep); font-size: 20px; font-weight: 600; line-height: 1.2; }
  .person-role { margin-bottom: 10px; }
  .address { margin-bottom: 4px; }
  .contact-line { display: flex; align-items: center; gap: 9px; height: 21px; }
  .contact-line svg { width: 13px; height: 13px; flex: none; fill: var(--brand-deep); }

  .brand-lockup {
    position: absolute;
    left: 0; right: 0; top: 118px;
    display: flex; align-items: center; justify-content: center; gap: 14px;
  }
  .brand-dot {
    width: 40px; height: 40px; border-radius: 50%;
    background: var(--brand-mid);
  }
  .brand-name {
    color: var(--brand-mid);
    font-size: 44px;
    font-weight: 600;
  }
  .brand-web {
    position: absolute;
    left: 0; right: 0; top: 222px;
    text-align: center;
    color: var(--brand-deep);
    font-size: 14px;
    letter-spacing: 4px;
  }
</style>
</head>
<body>
  <section class="card card-contact">
    <div class="contact-mark" role="img" aria-label="Velbrantix brand circle"></div>
    <div class="contact-divider"></div>
    <div class="contact-details">
      <p class="person-name">Adrian Holloway</p>
      <p class="person-role">CEO/Founder</p>
      <p>2214 Larkfield Road</p>
      <p class="address">Fairbourne, Oregon 97120</p>
      <p class="contact-line">
        <svg viewBox="0 0 16 16" aria-hidden="true"><path d="M3 1l3 3-1.5 2a9 9 0 0 0 5.5 5.5L12 10l3 3-2 2C7 15 1 9 1 3z"/></svg>
        503 218 4470
      </p>
      <p class="contact-line">
        <svg viewBox="0 0 16 16" aria-hidden="true"><rect x="4" y="1" width="8" height="4"/><rect x="1" y="6" width="14" height="6" rx="1"/><rect x="4" y="10" width="8" height="5"/></svg>
        503 218 4471
      </p>
      <p class="contact-line">
        <svg viewBox="0 0 16 16" aria-hidden="true"><path d="M1 3h14v10H1z M1 3l7 6 7-6" stroke="#141516" stroke-width="1"/></svg>
        adrian@velbrantix.net
      </p>
      <p class="contact-line">
        <svg viewBox="0 0 16 16" aria-hidden="true"><circle cx="8" cy="8" r="7"/><path d="M1 8h14M8 1c-3 4-3 10 0 14M8 1c3 4 3 10 0 14" stroke="#141516" stroke-width="1" fill="none"/></svg>
        www.velbrantix.net
      </p>
    </div>
  </section>

  <section class="card card-brand">
    <div class="brand-lockup">
      <span class="brand-dot"></span>
      <span class="brand-name">Velbrantix</span>
    </div>
    <p class="brand-web">www.velbrantix.net</p>
  </section>
</body>
</html>
```